New Webpage for High Class Expert Witness Services Company

We are looking for a minimalist design for a webpage that just has our logo and an entry form offer to connect with one of our Liaisons.
The entry form should just ask for Name, Email, Contact Info and Description of Project.

Company Name is: The Marlowe Crest Advisory Services

Number of Pages Required

1 page

```html
<!DOCTYPE html>
<html lang="en">
<head>
<meta charset="UTF-8">
<title>The Marlowe Crest Advisory Services — Connect with a Liaison</title>
<link href="https://fonts.googleapis.com/css2?family=Figtree:wght@300;400;500&display=swap" rel="stylesheet">
<style>
  :root {
    --page-bg: #ffffff;
    --ink: #111111;
    --brand-ink: #2b2b2b;
    --card-border: #dcdcdc;
    --field-border: #cfcfcf;
    --gold-top: #d3a757;
    --gold-bottom: #6d5733;
    --button-text: #ffffff;
  }
  * { box-sizing: border-box; margin: 0; padding: 0; }
  html, body {
    width: 1200px; height: 675px; overflow: hidden;
    background: var(--page-bg);
    font-family: "Figtree", sans-serif;
    color: var(--ink);
  }
  .page { position: relative; width: 1200px; height: 675px; }

  .brand-name {
    position: absolute; left: 475px; top: 84px; width: 275px;
    text-align: center;
    font-size: 17px; font-weight: 500; line-height: 21px;
    letter-spacing: 2px; text-transform: uppercase;
    color: var(--brand-ink);
  }

  .liaison-card {
    position: absolute; left: 427px; top: 164px;
    width: 355px; height: 414px;
    border: 1px solid var(--card-border);
    border-radius: 24px;
    background: var(--page-bg);
  }
  .card-title {
    position: absolute; left: 0; top: 20px; width: 100%;
    text-align: center;
    font-size: 23.5px; font-weight: 300; letter-spacing: -0.2px;
    white-space: nowrap;
  }
  .card-title strong { font-weight: 500; }
  .title-rule {
    position: absolute; left: 93px; top: 59px; width: 170px; height: 1px;
    background: linear-gradient(90deg, rgba(0,0,0,0), #444 50%, rgba(0,0,0,0));
  }

  .field-label {
    position: absolute; left: 45px;
    font-size: 11.5px; font-weight: 400;
  }
  .field-input {
    position: absolute; left: 46px; width: 264px; height: 34px;
    border: 1px solid var(--field-border);
    border-radius: 2px;
    background: var(--page-bg);
  }
  .field-area { height: 85px; }

  .connect-button {
    position: absolute; left: 45px; top: 358px; width: 265px; height: 35px;
    border: none; border-radius: 2px;
    background: linear-gradient(180deg, var(--gold-top), var(--gold-bottom));
    color: var(--button-text);
    font-family: "Figtree", sans-serif; font-size: 11.5px; font-weight: 400;
    display: flex; align-items: center; justify-content: center;
  }
</style>
</head>
<body>
<main class="page">
  <div class="brand-name">The Marlowe Crest<br>Advisory Services</div>

  <form class="liaison-card">
    <h1 class="card-title">Connect with one of our <strong>Liaisons</strong></h1>
    <div class="title-rule"></div>

    <label class="field-label" style="top:71px">Name</label>
    <div class="field-input" style="top:88px"></div>

    <label class="field-label" style="top:129px">Email</label>
    <div class="field-input" style="top:146px"></div>

    <label class="field-label" style="top:187px">Contact Info</label>
    <div class="field-input" style="top:204px"></div>

    <label class="field-label" style="top:245px">Description of Project</label>
    <div class="field-input field-area" style="top:262px"></div>

    <div class="connect-button">Connect with a Liaison</div>
  </form>
</main>
</body>
</html>
```